Real Estate Brokerage Stationery Designs

I am looking to have presentation folders with business card slots on both sides along with pockets on both sides. I've attached logos, website colors along with current business card designs.

I am looking for envelope designs both big and small. Possibly new business card designs, notepad templates for big and small notepads. Letterhead designs. Pop socket designs. Realtors name badge designs.

www.brightholdrealty.example

```html
<!DOCTYPE html>
<html lang="en">
<head>
<meta charset="utf-8">
<title>Brighthold Realty – Stationery Set</title>
<link href="https://fonts.googleapis.com/css2?family=Open+Sans:wght@400;600;700&family=Roboto+Condensed:wght@300;400&display=swap" rel="stylesheet">
<style>
:root{
  --backdrop:#8fb8e4;
  --brand-blue:#1c5fb8;
  --brand-deep:#1f3f8f;
  --brand-light:#4d8fd9;
  --paper:#ffffff;
  --body-gray:#7a7a7a;
  --strip-gray:#e9edf2;
}
*{box-sizing:border-box;margin:0;padding:0}
html,body{width:1200px;height:904px;overflow:hidden;background:var(--backdrop);font-family:"Open Sans",sans-serif}
.canvas{position:relative;width:1200px;height:904px}
.wordmark{font-family:"Open Sans",sans-serif;font-weight:700;color:var(--brand-deep);display:flex;align-items:center;gap:6px;white-space:nowrap}
.wordmark .mark-square{width:.8em;height:.8em;background:currentColor;display:inline-block;flex:none}
.wordmark.on-blue{color:var(--paper)}

/* Letterhead */
.letterhead{position:absolute;left:40px;top:30px;width:345px;height:490px;background:var(--paper);box-shadow:0 2px 6px rgba(0,0,0,.25)}
.letterhead .edge-accent{position:absolute;left:0;top:50px;width:4px;height:28px;background:var(--brand-blue)}
.letterhead .edge-accent.right{left:auto;right:0}
.letterhead .wordmark{position:absolute;top:60px;left:0;right:0;justify-content:center;font-size:17px}
.letterhead .body-copy{position:absolute;top:130px;left:38px;right:38px;font-family:"Roboto Condensed",sans-serif;font-weight:300;font-size:7.4px;line-height:1.55;color:var(--body-gray)}
.letterhead .body-copy p{margin-bottom:11px}
.letterhead .footer{position:absolute;left:0;right:0;bottom:0;height:28px}
.letterhead .footer-info{position:absolute;left:8px;top:6px;font-size:5.5px;color:var(--brand-deep);white-space:nowrap}
.letterhead .footer-rule{position:absolute;left:0;right:0;bottom:4px;height:3px;background:var(--brand-blue)}
.letterhead .footer-url{position:absolute;right:0;bottom:4px;height:16px;padding:0 10px 0 18px;background:var(--brand-blue);color:var(--paper);font-size:7px;font-weight:600;line-height:16px;clip-path:polygon(10px 0,100% 0,100% 100%,0 100%)}

/* Business cards */
.card{position:absolute;width:230px;height:130px;background:var(--paper);box-shadow:0 2px 6px rgba(0,0,0,.25);overflow:hidden}
.card-front{left:420px;top:24px}
.card-front .wordmark{position:absolute;top:42px;left:0;right:0;justify-content:center;font-size:15px}
.card-front .band{position:absolute;left:0;right:0;bottom:0;height:22px;background:var(--brand-blue);color:var(--paper);font-size:7px;font-weight:600;text-align:center;line-height:22px}
.card-front .band::before{content:"";position:absolute;left:0;right:0;top:-6px;height:6px;background:var(--strip-gray)}
.card-back{left:670px;top:24px}
.card-back .blue-side{position:absolute;left:0;top:0;bottom:0;width:110px;background:var(--brand-blue);display:flex;align-items:center;justify-content:center}
.card-back .blue-side .wordmark{font-size:9px;gap:4px}
.card-back .portrait{position:absolute;left:160px;top:12px;width:30px;height:34px;background:linear-gradient(#d8dde6,#9aa6b8)}
.card-back .details{position:absolute;left:118px;top:52px;right:6px;font-size:5.4px;line-height:1.6;color:var(--brand-deep);text-align:right}
.card-back .details .name{font-weight:700;font-size:7px}

/* Pop socket */
.popsocket{position:absolute;left:935px;top:20px;width:140px;height:140px;border-radius:50%;background:radial-gradient(circle at 40% 35%,var(--brand-light),var(--brand-blue) 70%);box-shadow:0 2px 6px rgba(0,0,0,.3);display:flex;flex-direction:column;align-items:center;justify-content:center;gap:8px}
.popsocket .wordmark{font-size:12px}
.popsocket .url{font-size:6.5px;color:var(--paper);font-weight:600}

/* Folder */
.folder{position:absolute;left:420px;top:180px;width:740px;height:390px;background:linear-gradient(160deg,#5f98da 0%,var(--brand-blue) 70%,#1a55a8 100%);box-shadow:0 3px 8px rgba(0,0,0,.3);overflow:hidden}
.folder .scene-wash{position:absolute;inset:0 0 52px 0;background:linear-gradient(180deg,rgba(255,255,255,.18),rgba(255,255,255,0) 60%)}
.folder .fold-line{position:absolute;left:370px;top:0;bottom:0;width:1px;background:rgba(0,0,0,.12)}
.folder svg.hexes{position:absolute;left:0;top:0}
.folder .wordmark{position:absolute;right:24px;top:40px;font-size:19px}
.folder .deals{position:absolute;left:30px;top:220px;color:var(--paper)}
.folder .deals-label{display:inline-block;background:linear-gradient(90deg,#d7e4f4,#8fb1dc);color:var(--brand-deep);font-weight:700;font-size:10px;padding:3px 22px 3px 30px;margin-bottom:8px}
.folder .deals ul{list-style:none;font-size:11px;font-weight:700;line-height:1.6}
.folder .deals li::before{content:"";display:inline-block;width:7px;height:7px;border-radius:50%;background:#b9d0ee;margin-right:8px;vertical-align:middle}
.folder .strip{position:absolute;left:0;right:0;bottom:0;height:52px;background:var(--paper)}
.folder .strip::before{content:"";position:absolute;left:0;right:0;top:0;height:3px;background:var(--brand-light)}
.folder .contact{position:absolute;left:24px;top:14px;font-size:8.5px;color:var(--brand-deep);line-height:1.6}
.folder .contact svg{width:8px;height:8px;vertical-align:-1px;margin-right:3px;fill:var(--brand-deep)}
.folder .strip-url{position:absolute;right:30px;top:18px;font-size:11px;font-weight:700;color:var(--brand-blue)}

/* Envelope */
.envelope{position:absolute;left:40px;top:560px;width:500px;height:300px;background:var(--paper);box-shadow:0 2px 6px rgba(0,0,0,.25)}
.envelope .wordmark{position:absolute;left:28px;top:30px;font-size:15px}
.envelope .return-address{position:absolute;left:28px;top:56px;font-size:7px;font-weight:700;color:var(--brand-deep);line-height:1.5}
.envelope .band{position:absolute;left:0;right:0;bottom:6px;height:3px;background:var(--brand-blue)}
.envelope .url-tab{position:absolute;right:0;bottom:6px;height:18px;padding:0 14px 0 24px;background:var(--brand-blue);color:var(--paper);font-size:9px;font-weight:600;line-height:18px;clip-path:polygon(12px 0,100% 0,100% 100%,0 100%)}

/* Notebook */
.notebook{position:absolute;left:940px;top:600px;width:210px;height:285px;background:linear-gradient(180deg,#2f74c8,var(--brand-blue));box-shadow:0 3px 8px rgba(0,0,0,.3);overflow:hidden;border-left:5px solid #1aa0c8}
.notebook .cover-photo{position:absolute;left:0;right:0;top:0;height:95px;background:linear-gradient(180deg,#a9cdee 0%,#d6c3a4 60%,#6f9a5a 100%)}
.notebook .cover-curve{position:absolute;left:-20px;right:-20px;top:78px;height:40px;background:var(--paper);border-radius:50% 50% 0 0/100% 100% 0 0;opacity:.9}
.notebook svg.hexes{position:absolute;left:0;top:110px}
.notebook .wordmark{position:absolute;left:66px;width:50px;top:168px;font-size:9px;white-space:normal;text-align:center;flex-direction:column;gap:3px;line-height:1.2}
.notebook .strip{position:absolute;left:0;right:0;bottom:0;height:24px;background:var(--paper);color:var(--brand-deep);font-size:7.5px;font-weight:700;text-align:center;line-height:24px}
.notebook .elastic{position:absolute;top:0;bottom:0;right:22px;width:8px;background:#3a3f47}
</style>
</head>
<body>
<div class="canvas">

  <section class="letterhead">
    <span class="edge-accent"></span><span class="edge-accent right"></span>
    <div class="wordmark"><span class="mark-square"></span>Brighthold Realty</div>
    <div class="body-copy">
      <p>Lorem Ipsum is simply dummy text of the printing and typesetting industry. Lorem Ipsum has been the industry's standard dummy text ever since the 1500s, when an unknown printer took a galley of type and scrambled it to make a type specimen book. It has survived not only five centuries, but also the leap into electronic typesetting, remaining essentially unchanged. It was popularised in the 1960s with the release of transfer sheets containing Lorem Ipsum passages, and more recently with desktop layout software including versions of Lorem Ipsum.</p>
      <p>It is a long established fact that a reader will be distracted by the readable content of a page when looking at its layout. The point of using Lorem Ipsum is that it has a more-or-less normal distribution of letters, as opposed to using 'Content here, content here', making it look like readable English. Many desktop publishing packages and web page editors now use Lorem Ipsum as their default model text, and a search for 'lorem ipsum' will uncover many web sites still in their infancy. Various versions have evolved over the years, sometimes by accident, sometimes on purpose (injected humour and the like).</p>
      <p>Contrary to popular belief, Lorem Ipsum is not simply random text. It has roots in a piece of classical Latin literature from 45 BC, making it over 2000 years old. Alan Merrow, a Latin professor at Northfield College, looked up one of the more obscure Latin words, consectetur, from a Lorem Ipsum passage, and going through the cites of the word in classical literature, discovered the undoubtable source. Lorem Ipsum comes from sections 1.10.32 and 1.10.33 of "de Finibus Bonorum et Malorum" structures, to generate Lorem Ipsum which looks reasonable. The generated Lorem Ipsum is therefore always free from repetition, injected humour, or non-characteristic words etc.</p>
    </div>
    <div class="footer">
      <div class="footer-info">410 Harbor Point Rd, Ste 12, Lakeview, FL 30000 · 555-010-2231</div>
      <div class="footer-rule"></div>
      <div class="footer-url">www.brightholdrealty.example</div>
    </div>
  </section>

  <section class="card card-front">
    <div class="wordmark"><span class="mark-square"></span>Brighthold Realty</div>
    <div class="band">www.northlanecards.example</div>
  </section>

  <section class="card card-back">
    <div class="blue-side"><div class="wordmark on-blue"><span class="mark-square"></span>Brighthold Realty</div></div>
    <div class="portrait" role="img" aria-label="Agent portrait photo"></div>
    <div class="details">
      <div class="name">Jordan Ellis</div>
      <div>Sales Associate</div>
      <div>410 Harbor Point Rd, Ste 12</div>
      <div>Lakeview, FL 30000</div>
      <div>555-010-2231 · 555-010-4478</div>
      <div>hello@brightholdrealty.example</div>
      <div>www.brightholdrealty.example</div>
    </div>
  </section>

  <section class="popsocket">
    <div class="wordmark on-blue"><span class="mark-square"></span>Brighthold Realty</div>
    <div class="url">www.brightholdrealty.example</div>
  </section>

  <section class="folder">
    <div class="scene-wash" role="img" aria-label="Faded blue-tinted photo of a residential street"></div>
    <div class="fold-line"></div>
    <svg class="hexes" width="740" height="340" viewBox="0 0 740 340">
      <defs>
        <linearGradient id="warm" x1="0" y1="0" x2="0" y2="1"><stop offset="0" stop-color="#d9c4a3"/><stop offset="1" stop-color="#8a6a45"/></linearGradient>
        <linearGradient id="cool" x1="0" y1="0" x2="0" y2="1"><stop offset="0" stop-color="#bcd6f2"/><stop offset="1" stop-color="#c9b48f"/></linearGradient>
        <linearGradient id="dusk" x1="0" y1="0" x2="0" y2="1"><stop offset="0" stop-color="#4a5f8c"/><stop offset="1" stop-color="#c99a62"/></linearGradient>
        <polygon id="hex" points="30,0 90,0 120,52 90,104 30,104 0,52"/>
      </defs>
      <g stroke="#ffffff" stroke-width="5" stroke-linejoin="round">
        <use href="#hex" x="225" y="40" fill="url(#warm)" role="img" aria-label="Photo of a home entrance"/>
        <use href="#hex" x="160" y="150" fill="url(#cool)" role="img" aria-label="Photo of a kitchen interior"/>
        <use href="#hex" x="250" y="245" fill="url(#dusk)" role="img" aria-label="Photo of a house at dusk"/>
        <use href="#hex" x="385" y="22" fill="url(#cool)" role="img" aria-label="Photo of a high-rise condominium"/>
        <use href="#hex" x="500" y="118" fill="url(#warm)" role="img" aria-label="Photo of a villa driveway"/>
        <use href="#hex" x="430" y="220" fill="url(#cool)" role="img" aria-label="Photo of a child's bedroom"/>
      </g>
    </svg>
    <div class="wordmark on-blue"><span class="mark-square"></span>Brighthold Realty</div>
    <div class="deals">
      <div class="deals-label">Deals In:</div>
      <ul>
        <li>Residential Real Estate</li>
        <li>Commercial Real Estate</li>
        <li>Property Management</li>
        <li>Investments</li>
      </ul>
    </div>
    <div class="strip">
      <div class="contact">
        <div><svg viewBox="0 0 10 10"><path d="M5 0a3.5 3.5 0 0 0-3.5 3.5C1.5 6 5 10 5 10s3.5-4 3.5-6.5A3.5 3.5 0 0 0 5 0zm0 5a1.5 1.5 0 1 1 0-3 1.5 1.5 0 0 1 0 3z"/></svg>410 Harbor Point Rd, Ste 12, Lakeview, FL 30000 · www.brightholdrealty.example</div>
        <div><svg viewBox="0 0 10 10"><path d="M2 0h2l1 2.5-1.3 1a6 6 0 0 0 2.8 2.8l1-1.3L10 6v2a2 2 0 0 1-2 2C3.6 10 0 6.4 0 2a2 2 0 0 1 2-2z"/></svg>555-010-2231 · 555-010-4478 · hello@brightholdrealty.example</div>
      </div>
      <div class="strip-url">www.brightholdrealty.example</div>
    </div>
  </section>

  <section class="envelope">
    <div class="wordmark"><span class="mark-square"></span>Brighthold Realty</div>
    <div class="return-address">410 Harbor Point Rd, Ste 12,<br>Lakeview, FL 30000</div>
    <div class="band"></div>
    <div class="url-tab">www.brightholdrealty.example</div>
  </section>

  <section class="notebook">
    <div class="cover-photo" role="img" aria-label="Photo of a suburban house with palm trees"></div>
    <div class="cover-curve"></div>
    <svg class="hexes" width="205" height="150" viewBox="0 0 205 150">
      <defs><polygon id="nhex" points="14,0 42,0 56,24 42,48 14,48 0,24"/></defs>
      <g stroke="#ffffff" stroke-width="2.5" fill="#c7b393">
        <use href="#nhex" x="8" y="0" role="img" aria-label="Photo of a home entrance"/>
        <use href="#nhex" x="120" y="0" fill="#bcd6f2" role="img" aria-label="Photo of a condominium tower"/>
        <use href="#nhex" x="8" y="52" fill="#d9c4a3" role="img" aria-label="Photo of a kitchen"/>
        <use href="#nhex" x="120" y="52" role="img" aria-label="Photo of a villa"/>
        <use href="#nhex" x="8" y="104" fill="#8a7a62" role="img" aria-label="Photo of a house at dusk"/>
        <use href="#nhex" x="120" y="104" fill="#9fc0e6" role="img" aria-label="Photo of a bedroom"/>
      </g>
    </svg>
    <div class="wordmark on-blue"><span class="mark-square"></span>Brighthold Realty</div>
    <div class="elastic"></div>
    <div class="strip">www.brightholdrealty.example</div>
  </section>

</div>
</body>
</html>
```